Klassisches Visitenkarten-Design mit braunen Farbtönen gesucht
Zielgruppe
Meine Firma bietet Pferdezahnbehandlungen, Pferdefütterungsberatung sowie Trensen- und Gebissanpassungen an. Ausserdem habe ich eine mobile Pferdewaage. Meine Kunden sind Pferdebesitzer der gehobenen Klasse, die gerne Geld in die Hand nehmen um ihr Tier korrekt zu halten/versorgen.
Ich setze bisher auf ein klassisches Design in braun Tönen.
Aufgabenstellung
Mir ist eine klare, schnörkellose Botschaft wichtig.
Ich möchte mich gerne mit klassischem, aber auch sehr schönem Design von der Konkurrenz abheben.
Der Fokus soll auf der wissenschaftlichen Arbeitsweise mit dem Partner Pferd liegen.
Im Anhang sind Fotos von der alten Visitenkarten. Dort fehlt mir aber die klare Linie.
Normalerweise arbeite ich mit der Schriftart Eurostyle, bin aber auch für neue Vorschläge offen.

```html
<!DOCTYPE html>
<html lang="de">
<head>
<meta charset="utf-8">
<title>HIPPOSAN Visitenkarten</title>
<link rel="stylesheet" href="https://fonts.googleapis.com/css2?family=Michroma&family=Exo+2:wght@400;500&display=swap">
<style>
  :root {
    --brown: #5c2411;
    --brown-text: #6b2c12;
    --paper: #ffffff;
    --backdrop: #f2f1ef;
  }
  * { margin: 0; padding: 0; box-sizing: border-box; }
  html, body { width: 1200px; height: 873px; overflow: hidden; background: var(--backdrop); }
  .stage {
    width: 1200px; height: 873px;
    display: flex; justify-content: center; align-items: center; gap: 110px;
  }
  .card {
    width: 360px; height: 556px;
    background: var(--paper);
    box-shadow: 0 2px 10px rgba(0,0,0,.12);
    position: relative; overflow: hidden;
  }
  /* Vorderseite */
  .card-front__brand-area {
    height: 345px; background: var(--brown);
    display: flex; align-items: center; justify-content: center;
  }
  .card-front__brand-mark {
    font-family: "Michroma", sans-serif; color: var(--paper);
    font-size: 34px; letter-spacing: 2px;
  }
  .card-front__info { padding: 26px 30px 0; }
  .card-front__name {
    font-family: "Michroma", sans-serif; color: var(--brown-text);
    font-size: 38px; letter-spacing: 1px; line-height: 1.1;
  }
  .card-front__services {
    list-style: none; margin-top: 14px;
    font-family: "Exo 2", sans-serif; color: var(--brown-text);
    font-size: 15px; letter-spacing: 1.2px; line-height: 1.5; text-transform: uppercase;
  }
  .card-front__services li:last-child { font-size: 19px; letter-spacing: .8px; }
  /* Rückseite */
  .card-back { display: flex; flex-direction: column; align-items: center; text-align: center; color: var(--brown-text); }
  .card-back__brand-mark {
    margin-top: 74px;
    font-family: "Michroma", sans-serif; font-size: 22px; letter-spacing: 2px; color: var(--brown);
  }
  .card-back__person { margin-top: 44px; }
  .card-back__person-name { font-family: "Michroma", sans-serif; font-size: 21px; letter-spacing: 1px; }
  .card-back__person-title { font-family: "Exo 2", sans-serif; font-size: 16px; letter-spacing: .8px; margin-top: 2px; }
  .card-back__contact {
    font-family: "Exo 2", sans-serif; font-style: normal;
    font-size: 16px; letter-spacing: 1px; line-height: 1.45;
  }
  .card-back__contact--address { margin-top: 28px; }
  .card-back__contact--reach { margin-top: 20px; }
</style>
</head>
<body>
<main class="stage">
  <article class="card card-front">
    <div class="card-front__brand-area">
      <span class="card-front__brand-mark">HIPPOSAN</span>
    </div>
    <div class="card-front__info">
      <h1 class="card-front__name">HIPPOSAN</h1>
      <ul class="card-front__services">
        <li>Pferdezahnbehandlung</li>
        <li>Pferdefütterungsberatung</li>
        <li>Mobile Pferdewaage</li>
      </ul>
    </div>
  </article>

  <article class="card card-back">
    <span class="card-back__brand-mark">HIPPOSAN</span>
    <div class="card-back__person">
      <h2 class="card-back__person-name">MARLENE S. KRONER</h2>
      <p class="card-back__person-title">Agrarwissenschaften (Dr. sc.)</p>
    </div>
    <address class="card-back__contact card-back__contact--address">
      Lindenweg 12<br>
      79999 Tannhofen/Südschwarzwald
    </address>
    <address class="card-back__contact card-back__contact--reach">
      0160 5550182<br>
      info@hipposan-zahn.com<br>
      www.hipposan.de
    </address>
  </article>
</main>
</body>
</html>
```